Design a product reviews website

We need a website design and simple logo for the brand Venlotix.com. The website will provide reviews of technology products and services. The brand and website should be approachable but should also be trustworthy and high quality. The deliverable should be designs, specs and assets that I can provide to a development team to build the website.

Target Market(s)

People researching products to buy.

Industry/Entity Type

Product

Logo Text

Venlotix.com

Number of Pages Required

5+ page

Font styles to use
Sans Serif

Colors
0492cd
0355a3
3176b5
33a6d7
85cae6
85abd2
cedeed
cee9f5

Requirements
Must have
• - Designs for the Homepage, Category and Article pages.
• - Designs for web and mobile.
• - Designs details for the engineering team to use for development.
• - I'm open to other colors than the preferences I chose but I'm more likely to like blues, greys and blacks.

```html
<!DOCTYPE html>
<html lang="en">
<head>
<meta charset="utf-8">
<title>Venlotix.com — Product Reviews</title>
<link href="https://fonts.googleapis.com/css2?family=Raleway:wght@300;400;500;600;700&display=swap" rel="stylesheet">
<style>
:root{
  --blue:#0492cd;
  --tag:#3b8bdc;
  --nav-active:#3f8ce0;
  --ink:#2a2a2a;
  --text:#555;
  --line:#d8d8d8;
  --panel:#f2f2f2;
  --white:#fff;
  --footer:#2b2b2b;
  --load:#8c8c8c;
}
*{box-sizing:border-box;margin:0;padding:0}
html,body{width:786px;height:1200px;overflow:hidden}
body{position:relative;background:var(--white);font-family:"Raleway",sans-serif;color:var(--ink)}
.abs{position:absolute}

.site-header{position:absolute;left:0;top:0;width:786px;height:54px;background:var(--white);border-bottom:2px solid var(--blue)}
.brand{position:absolute;left:67px;top:16px;display:flex;align-items:center;gap:6px;font-weight:700;font-size:18px;color:#1a2a3a;letter-spacing:.2px}
.brand-dot{width:11px;height:11px;background:var(--blue)}
.menu-toggle{position:absolute;left:720px;top:19px}

.hero{position:absolute;left:0;top:54px;width:786px;height:296px;background:
  radial-gradient(ellipse 150px 70px at 210px 170px,rgba(120,120,125,.55),transparent 70%),
  radial-gradient(ellipse 190px 45px at 560px 185px,rgba(110,110,118,.45),transparent 70%),
  radial-gradient(ellipse 60px 12px at 570px 210px,rgba(200,120,150,.35),transparent 80%),
  linear-gradient(180deg,#3d3a38 0%,#4a3f39 30%,#5e3f2e 55%,#6e3f28 75%,#5a3322 100%)}
.hero::after{content:"";position:absolute;inset:0;background:radial-gradient(ellipse at 50% 45%,transparent 40%,rgba(0,0,0,.35) 100%)}
.hero-title{position:absolute;z-index:1;left:0;width:786px;top:80px;text-align:center;color:#fff;font-weight:300;font-size:25px;line-height:27px;letter-spacing:.2px}
.search{position:absolute;z-index:1;left:226px;top:153px;width:338px;height:46px;background:rgba(255,255,255,.08)}
.search-input{position:absolute;left:17px;top:14px;width:254px;height:25px;background:#fff;font-size:9px;color:#888;padding:8px 10px}
.search-btn{position:absolute;left:274px;top:14px;width:39px;height:25px;background:var(--blue);display:flex;align-items:center;justify-content:center}

.category-nav{position:absolute;left:45px;top:386px;width:131px;border:1px solid var(--line);background:#fafafa}
.nav-item{height:32px;border-top:1px solid var(--line);display:flex;align-items:center;font-size:9px;color:#333;letter-spacing:.3px;padding-left:41px;position:relative}
.nav-item:first-child{border-top:none}
.nav-item.active{background:var(--nav-active);color:#fff;font-weight:600}
.nav-icon{position:absolute;left:10px;top:8px}

.panel{position:absolute;top:386px;height:720px;border:1px solid var(--line);background:var(--panel)}
.panel-title{height:28px;background:#fff;border-bottom:1px solid var(--line);font-weight:600;font-size:11.5px;letter-spacing:.3px;padding:8px 0 0 15px;color:#222}
.card{position:absolute;background:#fff}
.photo{position:absolute;left:0;top:0;width:100%}
.tag{position:absolute;background:var(--tag);color:#fff;font-weight:600;font-size:9.5px;height:21px;line-height:21px;padding:0 10px;letter-spacing:.2px}
.caption{position:absolute;left:8px;font-size:9.5px;color:var(--text);line-height:14px}
.rule{position:absolute;left:8px;right:8px;height:1px;background:#e3e3e3}
.author{position:absolute;left:7px;display:flex;align-items:center;gap:6px;font-size:11px;font-weight:500;color:var(--tag)}
.avatar{width:28px;height:28px;background:linear-gradient(#d4d6da,#9a9ea5)}
.posted{position:absolute;right:10px;font-size:8px;font-style:italic;color:#666}

.ph-theatre{background:
  radial-gradient(ellipse 90px 55px at 165px 55px,rgba(30,28,30,.85),transparent 75%),
  radial-gradient(ellipse 14px 60px at 22px 110px,rgba(40,36,34,.8),transparent 80%),
  radial-gradient(ellipse 14px 60px at 310px 110px,rgba(40,36,34,.8),transparent 80%),
  linear-gradient(180deg,#b4603a 0%,#a9532f 55%,#c29a6a 70%,#4a3a30 82%,#8a6a50 100%)}
.ph-panel{background:
  radial-gradient(ellipse 45px 40px at 70px 85px,rgba(214,160,120,.8),transparent 75%),
  linear-gradient(90deg,#6e5a46 0%,#a59684 30%,#e4e6e8 55%,#f3f3f3 100%)}
.ph-phone{background:
  radial-gradient(ellipse 28px 55px at 95px 60px,rgba(60,70,90,.6),transparent 80%),
  radial-gradient(ellipse 30px 20px at 45px 85px,rgba(230,130,50,.55),transparent 80%),
  linear-gradient(135deg,#f6f6f6,#e2e3e6 60%,#f2f2f2)}
.ph-speaker{background:
  radial-gradient(ellipse 40px 20px at 300px 150px,rgba(230,215,190,.6),transparent 80%),
  linear-gradient(180deg,transparent 80%,rgba(110,70,40,.8) 100%),
  linear-gradient(90deg,#8a4a34 0%,#6a3c2c 12%,#262626 17%,#1c1c1c 70%,#3a3a3a 82%,#d8cfc0 100%)}
.ph-pots{background:
  radial-gradient(ellipse 50px 30px at 45px 55px,rgba(220,140,90,.8),transparent 80%),
  radial-gradient(ellipse 45px 28px at 110px 45px,rgba(200,120,80,.7),transparent 80%),
  linear-gradient(180deg,#2a2a2a 0%,#4a3a32 40%,#a8a8a8 70%,#3a3a3a 100%)}
.ph-sink{background:
  radial-gradient(ellipse 40px 25px at 80px 70px,rgba(190,195,200,.8),transparent 80%),
  linear-gradient(180deg,#c8c6be 0%,#aaa79c 35%,#1e1e1e 48%,#9a6a42 60%,#7a5232 100%)}
.ph-tablet{background:
  radial-gradient(ellipse 50px 35px at 85px 45px,rgba(80,160,120,.6),transparent 80%),
  linear-gradient(170deg,#c89a3c 0%,#7a7a5a 25%,#2e66c0 55%,#2050a8 80%,#1a1a1a 100%)}
.ph-lock{background:
  radial-gradient(ellipse 22px 40px at 90px 45px,rgba(60,60,64,.8),transparent 80%),
  linear-gradient(90deg,#4a7aa8 0%,#9ab2c8 18%,#dadde0 40%,#c8ccd0 60%,#b8915e 80%,#d8c9b0 100%)}

.load-more{position:absolute;left:198px;top:1120px;width:545px;height:31px;background:var(--load);color:#fff;font-size:10px;font-weight:600;display:flex;align-items:center;justify-content:center;gap:8px}
.site-footer{position:absolute;left:0;top:1168px;width:786px;height:32px;background:var(--footer);color:#ddd;font-size:9px;text-align:center;line-height:32px}
</style>
</head>
<body>

<header class="site-header">
  <div class="brand"><span class="brand-dot"></span>Venlotix.com</div>
  <svg class="menu-toggle" width="15" height="13" viewBox="0 0 15 13" aria-label="Menu">
    <g fill="#1e2a38"><rect x="0" y="0" width="3.5" height="3.5"/><rect x="5" y="0" width="10" height="3.5"/><rect x="0" y="4.7" width="3.5" height="3.5"/><rect x="5" y="4.7" width="10" height="3.5"/><rect x="0" y="9.4" width="3.5" height="3.5"/><rect x="5" y="9.4" width="10" height="3.5"/></g>
  </svg>
</header>

<section class="hero" role="img" aria-label="Photo of a smartwatch and a fitness band on a wooden table">
  <h1 class="hero-title">The Best Product And Services Reviews<br>And Rankings</h1>
  <div class="search">
    <div class="search-input">Search</div>
    <div class="search-btn">
      <svg width="12" height="12" viewBox="0 0 12 12"><circle cx="5" cy="5" r="3.6" fill="none" stroke="#fff" stroke-width="1.8"/><line x1="7.7" y1="7.7" x2="11" y2="11" stroke="#fff" stroke-width="2"/></svg>
    </div>
  </div>
</section>

<nav class="category-nav">
  <div class="nav-item active"><svg class="nav-icon" width="18" height="15" viewBox="0 0 18 15"><path d="M9 0 L18 8 H15 V15 H11 V10 H7 V15 H3 V8 H0Z" fill="#fff"/></svg>HOME</div>
  <div class="nav-item"><svg class="nav-icon" width="14" height="16" viewBox="0 0 14 16"><rect x="1" y="0" width="12" height="16" rx="2" fill="#555"/><rect x="4" y="6" width="9" height="4" fill="#fff"/></svg>APPLIANCES</div>
  <div class="nav-item"><svg class="nav-icon" width="18" height="15" viewBox="0 0 18 15"><rect x="1" y="1" width="16" height="10" fill="none" stroke="#555" stroke-width="1.4"/><rect x="6" y="13" width="6" height="1.5" fill="#555"/></svg>COMPUTERS</div>
  <div class="nav-item"><svg class="nav-icon" width="22" height="14" viewBox="0 0 22 14"><rect x="0" y="1" width="22" height="12" rx="2" fill="#555"/><circle cx="15" cy="7" r="3.5" fill="#fff"/><rect x="3" y="4" width="6" height="1.5" fill="#fff"/><rect x="3" y="8" width="6" height="1.5" fill="#fff"/></svg>ELECTRONICS</div>
  <div class="nav-item"><svg class="nav-icon" width="22" height="16" viewBox="0 0 22 16"><path d="M1 8 L8 2 L15 8 M3 7 V15 H13 V7" fill="none" stroke="#555" stroke-width="1.3"/><path d="M16 4 L21 5.5 V9 C21 12 18.5 13.5 16 14 C13.5 13.5 12 12 12 9" fill="#fff" stroke="#555" stroke-width="1.2"/></svg>HOME SECURITY</div>
  <div class="nav-item"><svg class="nav-icon" width="14" height="16" viewBox="0 0 14 16"><rect x="3" y="0" width="8" height="15" rx="1.5" fill="none" stroke="#555" stroke-width="1.4"/><circle cx="7" cy="12.5" r=".9" fill="#555"/></svg>MOBILES</div>
  <div class="nav-item"><svg class="nav-icon" width="18" height="16" viewBox="0 0 18 16"><path d="M1 8 L9 1 L17 8 M3 7 V15 H15 V7" fill="none" stroke="#555" stroke-width="1.2"/><rect x="7" y="8" width="4" height="4" fill="none" stroke="#555"/></svg>SMART HOME</div>
  <div class="nav-item"><svg class="nav-icon" width="18" height="16" viewBox="0 0 18 16"><rect x="5" y="4" width="8" height="8" fill="#555"/><g stroke="#555" stroke-width="1"><line x1="2" y1="6" x2="16" y2="6"/><line x1="2" y1="8" x2="16" y2="8"/><line x1="2" y1="10" x2="16" y2="10"/><line x1="7" y1="1" x2="7" y2="15"/><line x1="9" y1="1" x2="9" y2="15"/><line x1="11" y1="1" x2="11" y2="15"/></g></svg>SOFTWARE</div>
</nav>
<svg class="abs" style="left:149px;top:408px" width="10" height="13" viewBox="0 0 10 13"><path d="M3 1 V8 L1.5 7 L1 8 L4 12 H8.5 L9 7 L5 6 V1Z" fill="#fff" stroke="#222" stroke-width=".8"/></svg>

<section class="panel" style="left:198px;width:354px">
  <div class="panel-title">NEW PRODUCTS</div>

  <article class="card" style="left:11px;top:42px;width:331px;height:236px">
    <div class="photo ph-theatre" role="img" aria-label="Photo of a home theatre with wall TV and tower speakers" style="height:158px"></div>
    <span class="tag" style="left:208px;top:126px">HOME</span>
    <span class="tag" style="left:261px;top:126px">SPEAKERS</span>
    <p class="caption" style="top:168px">Lorem Ipsum Dolor Sit Amet</p>
    <div class="rule" style="top:189px"></div>
    <div class="author" style="top:196px"><span class="avatar"></span>Aaron Pell</div>
    <span class="posted" style="top:206px">Posted On 11 Aug, 2016</span>
  </article>

  <article class="card" style="left:11px;top:294px;width:153px;height:164px">
    <div class="photo ph-panel" role="img" aria-label="Photo of a hand using a smart home wall panel" style="height:120px"></div>
    <span class="tag" style="left:94px;top:91px">HOME</span>
    <p class="caption" style="left:6px;top:127px">Lorem ipsum dolor sit amet,<br>consectetuer elit</p>
  </article>

  <article class="card" style="left:189px;top:294px;width:153px;height:164px">
    <div class="photo ph-phone" role="img" aria-label="Photo of a smartphone and smartwatch" style="height:120px"></div>
    <span class="tag" style="left:94px;top:91px">HOME</span>
    <p class="caption" style="left:6px;top:127px">Lorem ipsum dolor sit amet,<br>consectetuer elit</p>
  </article>

  <article class="card" style="left:11px;top:479px;width:331px;height:236px">
    <div class="photo ph-speaker" role="img" aria-label="Photo of a black wireless speaker on a wooden table" style="height:158px"></div>
    <span class="tag" style="left:267px;top:127px">AUDIO</span>
    <p class="caption" style="top:168px">Lorem Ipsum Dolor Sit Amet</p>
    <div class="rule" style="top:189px"></div>
    <div class="author" style="top:196px"><span class="avatar"></span>Aaron Pell</div>
    <span class="posted" style="top:206px">Posted On 11 Aug, 2016</span>
  </article>
</section>

<aside class="panel" style="left:574px;width:169px">
  <div class="panel-title" style="padding-left:10px">POPULAR PRODUCTS</div>

  <article class="card" style="left:10px;top:42px;width:148px;height:156px">
    <div class="photo ph-pots" role="img" aria-label="Photo of copper cooking pots" style="height:112px"></div>
    <span class="tag" style="left:88px;top:82px">HOME</span>
    <p class="caption" style="top:120px">Lorem ipsum dolor sit<br>amet, consectetuer</p>
  </article>

  <article class="card" style="left:10px;top:214px;width:148px;height:156px">
    <div class="photo ph-sink" role="img" aria-label="Photo of a kitchen sink with a modern faucet" style="height:112px"></div>
    <span class="tag" style="left:88px;top:82px">HOME</span>
    <p class="caption" style="top:120px">Lorem ipsum dolor sit<br>amet, consectetuer</p>
  </article>

  <article class="card" style="left:10px;top:386px;width:148px;height:156px">
    <div class="photo ph-tablet" role="img" aria-label="Photo of a tablet with a blue keyboard cover" style="height:112px"></div>
    <span class="tag" style="left:88px;top:82px">HOME</span>
    <p class="caption" style="top:120px">Lorem ipsum dolor sit<br>amet, consectetuer</p>
  </article>

  <article class="card" style="left:10px;top:558px;width:148px;height:156px">
    <div class="photo ph-lock" role="img" aria-label="Photo of a keypad door lock" style="height:112px"></div>
    <span class="tag" style="left:88px;top:82px">HOME</span>
    <p class="caption" style="top:120px">Lorem ipsum dolor sit<br>amet, consectetuer</p>
  </article>
</aside>

<div class="load-more">
  <svg width="16" height="16" viewBox="0 0 16 16"><path d="M13 8 A5 5 0 1 1 11 4" fill="none" stroke="#fff" stroke-width="1.6"/><path d="M9.5 2 L12.5 4 L10 6.5" fill="none" stroke="#fff" stroke-width="1.6"/></svg>
  Load More
</div>

<footer class="site-footer">Copyright © 2016 &nbsp;Venlotix.com. All Rights Reserved.</footer>

</body>
</html>
```